Full re-design of visual identity

We have just re-designed our logo and would like to apply it on our folders, business cards, stationery, and etc... we are attaching new logo + the material we need to re-design... we will provide full corel draw files to help make job easier and also because lot of icons and artwork can be still used...

any doubts we are at your disposal. thanks in advance.

```html
<!DOCTYPE html>
<html lang="en">
<head>
<meta charset="utf-8">
<title>Orbilink — Stationery Identity</title>
<link rel="stylesheet" href="https://fonts.googleapis.com/css2?family=Titillium+Web:wght@400;700&family=Tinos&display=swap">
<style>
:root{
  --bg:#f0f0f0;
  --paper:#fbfbfb;
  --orange:#e2660f;
  --orange-deep:#c8520d;
  --ink:#6d6d6d;
  --text:#2a2a2a;
  --muted:#9a9a9a;
  --faint:#e4e4e4;
}
*{margin:0;padding:0;box-sizing:border-box}
html,body{width:1200px;height:795px;overflow:hidden;background:var(--bg)}
.canvas{position:relative;width:1200px;height:795px;font-family:"Titillium Web",Arial,sans-serif}
.piece{position:absolute;background:var(--paper);overflow:hidden}

.brand{display:flex;align-items:center;gap:3px;font-family:"Titillium Web",Arial,sans-serif;font-weight:700;color:var(--ink);line-height:1;letter-spacing:-.02em;white-space:nowrap}
.brand .dot{border-radius:50%;background:var(--orange);flex:none}
.tagline{font-family:"Titillium Web",Arial,sans-serif;font-weight:400;color:var(--muted);letter-spacing:.02em;white-space:nowrap}
.deco{position:absolute;border-radius:50%;background:var(--faint)}

/* Letterhead */
.letterhead{left:297px;top:38px;width:276px;height:370px}
.letterhead .brand{position:absolute;left:41px;top:20px;font-size:19px}
.letterhead .brand .dot{width:9px;height:9px}
.letterhead .tagline{position:absolute;left:42px;top:38px;font-size:4.5px}
.letterhead .deco{left:185px;top:-20px;width:80px;height:80px}
.letter-body{position:absolute;left:40px;top:76px;width:206px;font-family:"Tinos","Times New Roman",serif;font-size:5.2px;line-height:6.9px;color:var(--text);text-align:justify}
.letter-body p{margin-bottom:6px}
.letter-body .closing{margin-top:40px;margin-bottom:0}
.signature{width:38px;height:12px;background:#e9e9e9;margin:2px 0}
.contact-list{position:absolute;left:36px;top:325px;list-style:none;font-size:3.6px;line-height:6px;color:var(--muted)}
.contact-list li{display:flex;align-items:center;gap:6px}
.contact-list li::before{content:"";width:3px;height:3px;border-radius:50%;background:var(--orange)}
.footer-band{position:absolute;left:0;bottom:0;width:276px;height:14px}

/* Folder */
.folder{left:597px;top:36px;width:302px;height:385px;background:linear-gradient(160deg,var(--orange) 0%,var(--orange-deep) 100%)}
.folder .deco{background:rgba(255,255,255,.06)}
.folder .deco.top{left:160px;top:-40px;width:150px;height:150px}
.folder .deco.bottom{left:40px;top:260px;width:120px;height:120px}
.folder .brand{position:absolute;left:92px;top:164px;font-size:30px;color:#fff}
.folder .brand .dot{width:14px;height:14px;background:#fff}
.folder .tagline{position:absolute;left:96px;top:191px;font-size:6px;color:#ffe2cc}

/* Business cards */
.card-front{left:295px;top:437px;width:130px;height:63px}
.card-front .brand{position:absolute;left:14px;top:6px;font-size:13px}
.card-front .brand .dot{width:6px;height:6px}
.card-front .tagline{position:absolute;left:15px;top:19px;font-size:3px}
.card-front .holder{position:absolute;right:12px;top:25px;text-align:right;font-size:4px;line-height:5px;color:var(--text)}
.card-front .holder .role{color:var(--orange)}
.card-front .contact-list{left:10px;top:31px;font-size:2.8px;line-height:4.6px}
.card-front .footer-band{width:130px;height:7px}
.card-back{left:453px;top:437px;width:120px;height:65px}
.card-back .deco{left:72px;top:-14px;width:58px;height:58px;background:var(--orange)}
.card-back .brand{position:absolute;left:11px;top:44px;font-size:13px}
.card-back .brand .dot{width:6px;height:6px}

/* Envelopes */
.envelope-back{left:613px;top:447px;width:290px;height:143px}
.envelope-back .flap{position:absolute;left:0;top:0}
.envelope-back .dot-mark{position:absolute;left:139px;top:14px;width:12px;height:12px;border-radius:50%;background:var(--orange)}
.envelope-front{left:613px;top:612px;width:292px;height:146px}
.envelope-front .brand{position:absolute;left:28px;top:18px;font-size:22px}
.envelope-front .brand .dot{width:10px;height:10px}
.envelope-front .tagline{position:absolute;left:30px;top:40px;font-size:5px}
.envelope-front .deco{left:182px;top:6px;width:92px;height:92px}

/* Notebook */
.notebook{left:318px;top:565px;width:110px;height:195px}
.notebook .spiral{position:absolute;left:0;top:4px}
.notebook .brand{position:absolute;left:8px;top:88px;font-size:17px}
.notebook .brand .dot{width:8px;height:8px}
.notebook .tagline{position:absolute;left:10px;top:104px;font-size:3.4px}

/* Key tag & eraser */
.key-tag{left:466px;top:560px;width:39px;height:105px;border-radius:5px}
.key-tag .dot{position:absolute;left:13px;top:46px;width:12px;height:12px;border-radius:50%;background:var(--orange)}
.key-tag .brand{position:absolute;left:5px;top:66px;font-size:9px}
.eraser{left:474px;top:682px;width:27px;height:78px}
.eraser .dot{position:absolute;left:8px;top:38px;width:11px;height:11px;border-radius:50%;background:var(--orange)}
</style>
</head>
<body>
<main class="canvas">

  <section class="piece letterhead">
    <span class="deco"></span>
    <div class="brand">Orbilink<span class="dot"></span></div>
    <div class="tagline">telecom · technology · internet</div>
    <div class="letter-body">
      <p>Gentlemen,</p>
      <p>Enclosed I have the honor to send you an article which I should be pleased if you would accept for the "Harbor Review". I am <em>desperately</em> pushed for money; and in the event of Mr. Hallowell's liking the "Landscape-Garden", I would take it as an especial favor if you would mail me the amount due for it, so as to reach me here by the 21st, on which day I shall need it. Can you possibly oblige me in this? If you accept the paper I presume you will allow me your usual rates, whatever that is for similar contributions—but I set <em>no price</em>—leaving all to your own liberality. The piece will make 8 of your pages and rather more.</p>
      <p>Will you be kind enough to put the best possible interpretation upon my behavior while in the city? You must have conceived a <em>queer</em> idea of me—but the simple truth is that Whitcombe would insist <em>upon the juleps</em>, and I knew not what I was either doing or saying. The Review of Duncs which I offered you was deficient in a 1/2 page of commencement, which I had written to supersede the old beginning, and which gave the article the character of a general and retrospective review. No wonder you did not take it—I would have been very much mortified if you had. I hope to see you at some future time, under better auspices.</p>
      <p class="closing">In the meantime I remain<br>Yours very truly,</p>
      <div class="signature" role="img" aria-label="Handwritten signature"></div>
      <p>Elias Marrow</p>
    </div>
    <ul class="contact-list">
      <li>+1 555 0142</li>
      <li>+1 555 0178</li>
      <li>hello@orbilink.test</li>
      <li>www.orbilink.test</li>
    </ul>
    <svg class="footer-band" viewBox="0 0 276 14" preserveAspectRatio="none"><path d="M0 14 L0 6 Q138 -4 276 6 L276 14 Z" fill="var(--orange)"/></svg>
  </section>

  <section class="piece folder">
    <span class="deco top"></span>
    <span class="deco bottom"></span>
    <div class="brand">Orbilink<span class="dot"></span></div>
    <div class="tagline">telecom · technology · internet</div>
  </section>

  <section class="piece card-front">
    <div class="brand">Orbilink<span class="dot"></span></div>
    <div class="tagline">telecom · technology · internet</div>
    <div class="holder">Dana Reyes<br><span class="role">Director</span></div>
    <ul class="contact-list">
      <li>+1 555 0142</li>
      <li>+1 555 0178</li>
      <li>dana@orbilink.test</li>
      <li>www.orbilink.test</li>
    </ul>
    <svg class="footer-band" viewBox="0 0 130 7" preserveAspectRatio="none"><path d="M0 7 L0 3 Q65 -2 130 3 L130 7 Z" fill="var(--orange)"/></svg>
  </section>

  <section class="piece card-back">
    <span class="deco"></span>
    <div class="brand">Orbilink<span class="dot"></span></div>
  </section>

  <section class="piece envelope-back">
    <svg class="flap" width="290" height="50" viewBox="0 0 290 50"><path d="M0 0 L20 48 L270 48 L290 0" fill="none" stroke="#e2e2e2" stroke-width="1"/></svg>
    <span class="dot-mark"></span>
  </section>

  <section class="piece envelope-front">
    <span class="deco"></span>
    <div class="brand">Orbilink<span class="dot"></span></div>
    <div class="tagline">telecom · technology · internet</div>
  </section>

  <section class="piece notebook">
    <svg class="spiral" width="8" height="188" viewBox="0 0 8 188">
      <g stroke="#555" stroke-width="1" fill="none">
        <path d="M1 6h6M1 14h6M1 22h6M1 30h6M1 38h6M1 46h6M1 54h6M1 62h6M1 70h6M1 78h6M1 86h6M1 94h6M1 102h6M1 110h6M1 118h6M1 126h6M1 134h6M1 142h6M1 150h6M1 158h6M1 166h6M1 174h6M1 182h6"/>
      </g>
    </svg>
    <div class="brand">Orbilink<span class="dot"></span></div>
    <div class="tagline">telecom · technology · internet</div>
  </section>

  <section class="piece key-tag">
    <span class="dot"></span>
    <div class="brand">Orbilink</div>
  </section>

  <section class="piece eraser">
    <span class="dot"></span>
  </section>

</main>
</body>
</html>
```